Roofing company in Toronto, Canada needs a logo design and business card design

We need a business card and logo created for our company. Our company is "KLV Roofing" which provides roofing services for commercial and residential customers. We serve customers in the Greater Toronto Area (in Canada) thus the name KLV.

We want the logo and business card to be a modern design displaying professionalism and quality in the work. We would prefer rounded corners for the business cards but are open to other ideas. The cards should be pleasant and appealing to customers.

Target Market(s)

Commercial and Residential customers

Industry/Entity Type

Roofing

Contact Information for Business Card

Logo Text

KLV Roofing

Requirements
Nice to have
• Colours that are pleasing to the eye but at the same time should stand out from other business cards. If the design can incorporate the name of KLV Roofing and the actual concept of roofing that would be nice.
Should not have
• Do not want the business cards or logo to be childish looking. Need to look professionally designed.

```html
<!DOCTYPE html>
<html lang="en">
<head>
<meta charset="utf-8">
<title>KLV Roofing – Business Card</title>
<link href="https://fonts.googleapis.com/css2?family=Open+Sans:wght@400;700&display=swap" rel="stylesheet">
<style>
  :root {
    --page-bg: #ece6dd;
    --card-dark: #2e2e2e;
    --roof-tan: #b3804c;
    --text-light: #ffffff;
    --text-muted: #8a8a8a;
    --icon-grey: #9a9a9a;
  }
  * { margin: 0; padding: 0; box-sizing: border-box; }
  html, body {
    width: 1193px; height: 1200px; overflow: hidden;
    background: var(--page-bg);
    font-family: "Open Sans", sans-serif;
  }
  .canvas { position: relative; width: 1193px; height: 1200px; }
  .card {
    position: absolute; left: 177px; width: 838px; height: 502px;
    background: var(--card-dark); overflow: hidden;
    box-shadow: 0 14px 24px rgba(0,0,0,0.25);
  }
  .card--front { top: 46px; }
  .card--back { top: 612px; }

  .brand { display: flex; align-items: center; gap: 20px; color: var(--roof-tan); font-weight: 700; }
  .brand__mark { background: var(--roof-tan); }
  .card--front .brand {
    position: absolute; left: 0; right: 0; top: 0; bottom: 0; justify-content: center;
    font-size: 84px; letter-spacing: 1px;
  }
  .card--front .brand__mark { width: 58px; height: 58px; }
  .card--back .brand {
    position: absolute; left: 80px; top: 110px; font-size: 40px; gap: 12px;
  }
  .card--back .brand__mark { width: 28px; height: 28px; }

  .card__shapes { position: absolute; inset: 0; }

  .person { position: absolute; left: 82px; top: 220px; }
  .person__name { color: var(--text-light); font-weight: 700; font-size: 36px; line-height: 1.1; }
  .person__role { color: var(--text-muted); font-size: 17px; margin-top: 4px; }

  .contacts { position: absolute; left: 80px; top: 334px; list-style: none; }
  .contacts li {
    display: flex; align-items: center; gap: 12px;
    color: var(--text-light); font-size: 18px; height: 24px; margin-bottom: 8px;
  }
  .contacts li:nth-child(1) { margin-bottom: 11px; }
  .contacts li:nth-child(3) { margin-bottom: 11px; }
  .contacts svg { width: 18px; height: 18px; flex: none; }
</style>
</head>
<body>
<div class="canvas">

  <section class="card card--front">
    <div class="brand"><span class="brand__mark"></span><span class="brand__name">KLV Roofing</span></div>
  </section>

  <section class="card card--back">
    <svg class="card__shapes" viewBox="0 0 1048 627" preserveAspectRatio="none" aria-hidden="true">
      <polygon points="559,0 1048,0 1048,627 709,627 861,377" fill="var(--roof-tan)"/>
      <line x1="562" y1="-4" x2="864" y2="377" stroke="#fff" stroke-width="11"/>
      <line x1="1052" y1="84" x2="710" y2="632" stroke="#fff" stroke-width="11"/>
    </svg>

    <div class="brand"><span class="brand__mark"></span><span class="brand__name">KLV Roofing</span></div>

    <div class="person">
      <h1 class="person__name">Mark Delaney</h1>
      <p class="person__role">general director</p>
    </div>

    <ul class="contacts">
      <li>
        <svg viewBox="0 0 18 18"><rect x="4" y="1" width="10" height="16" rx="2" fill="none" stroke="var(--icon-grey)" stroke-width="2"/><rect x="7.5" y="13" width="3" height="1.5" fill="var(--icon-grey)"/></svg>
        416 55 20 194
      </li>
      <li>
        <svg viewBox="0 0 18 18"><rect x="1" y="4" width="16" height="11" fill="var(--icon-grey)"/><polyline points="1,4 9,10 17,4" fill="none" stroke="var(--card-dark)" stroke-width="1.5"/></svg>
        mdelaney@klvroofing.com
      </li>
      <li>
        <svg viewBox="0 0 18 18" fill="none" stroke="var(--icon-grey)" stroke-width="1.4"><circle cx="9" cy="9" r="7.5"/><ellipse cx="9" cy="9" rx="3.2" ry="7.5"/><line x1="1.5" y1="9" x2="16.5" y2="9"/><line x1="2.5" y1="5.5" x2="15.5" y2="5.5"/><line x1="2.5" y1="12.5" x2="15.5" y2="12.5"/></svg>
        www.klvroofing.com
      </li>
      <li>
        <svg viewBox="0 0 18 18"><path d="M9 1a5.5 5.5 0 0 0-5.5 5.5C3.5 11 9 17 9 17s5.5-6 5.5-10.5A5.5 5.5 0 0 0 9 1z" fill="var(--icon-grey)"/><circle cx="9" cy="6.5" r="2" fill="var(--card-dark)"/></svg>
        88 Harbourline Ave, Canada
      </li>
    </ul>
  </section>

</div>
</body>
</html>
```